tinyTally Resource Book - 10 maths tasks to do outside

I need a 22 (11 pages back to back) page A6 sized book produced to standard for submission to professional printer. Needs to be as .pdf file showing guide lines and allowances for colour bleed. I have text already written and submitted as attachment in a Word file with margins set to A6 size. The theme of the materials is "Nature Play" so using lots of pictures from nature (Australia preferably) and showing lots of patterns in nature (rocks, leaves, flower petals etc). Some of the tasks refer to specific activities, such as "shadows" and "floating" so would be great to illustrate appropriately. The big emphasis is on learning outside the classroom, getting kids to engage actively with nature. I would like to see the pages as full colour - so not white background. The book itself will be spiral bound along the top edge so a margin of at least 1cm will be required at the top of each page (or the bottom of even numbered pages). Book will be printed on plastic laminated matte paper for outdoor use. Font size needs to be big enough to read. Fonts sizes, alignments and page numbers are all different at the moment and need to be standardised. One photo is included in a page as a sample if you can use it, otherwise disregard. Logo for Wattlebrook Numeracy Guild is also included to have as part of the acknowledgements at the back of the book.

Target Market(s)

Book is for early childhood and preschool teachers.

Industry/Entity Type

Education

Font styles to use
Sans Serif

Requirements
Must have
• Colour and appeal.
Nice to have
• Use of natural colours instead of bright catchy colours but that is your call.
Should not have
• American spelling

```html
<!DOCTYPE html>
<html lang="en-AU">
<head>
<meta charset="utf-8">
<title>8. Does It Float? – tinyTally Resource Book</title>
<link rel="stylesheet" href="https://fonts.googleapis.com/css2?family=PT+Sans:ital,wght@0,700;1,700&family=Didact+Gothic&display=swap">
<style>
  :root {
    --ink-navy: #2c3d8c;
    --ink-body: #262a33;
    --bullet-red: #d6262c;
    --water-top: #ffffff;
    --water-mid: #cfe6f3;
    --water-deep: #6fb2da;
    --paper: #ffffff;
    --crop: #333333;
  }
  * { margin: 0; padding: 0; box-sizing: border-box; }
  html, body { width: 892px; height: 1200px; overflow: hidden; background: var(--paper); }
  .sheet { position: relative; width: 892px; height: 1200px; }
  .crop-marks { position: absolute; inset: 0; }
  .page-bleed {
    position: absolute; left: 52px; top: 52px; width: 788px; height: 1094px;
    background: linear-gradient(180deg, var(--water-top) 0%, #f4f9fc 30%, var(--water-mid) 55%, #9fcde8 78%, var(--water-deep) 100%);
  }
  .page-content { position: absolute; inset: 0; }
  .task-title, .outcome-title {
    position: absolute; left: 0; width: 892px; text-align: center;
    font-family: "PT Sans", sans-serif; font-weight: 700; color: var(--ink-navy);
  }
  .task-title { top: 100px; font-size: 50px; line-height: 56px; }
  .outcome-title { top: 178px; font-size: 31px; line-height: 42px; }
  .lead-in {
    position: absolute; left: 124px;
    font-family: "PT Sans", sans-serif; font-weight: 700; font-style: italic;
    color: var(--ink-navy); font-size: 25px; line-height: 36px;
  }
  .lead-in.skills { top: 269px; width: 640px; }
  .lead-in.educators { top: 550px; }
  .lead-in.task { top: 813px; }
  .body-text {
    position: absolute; left: 196px;
    font-family: "Didact Gothic", sans-serif; color: var(--ink-body);
    font-size: 32px; line-height: 45.5px;
  }
  .body-text.children { top: 414px; }
  .body-text.educators { top: 586px; }
  .opportunities {
    position: absolute; left: 192px; top: 850px; list-style: none;
    font-family: "Didact Gothic", sans-serif; color: var(--ink-body);
    font-size: 29px; line-height: 42px;
  }
  .opportunities li { position: relative; padding-left: 26px; }
  .opportunities li::before {
    content: ""; position: absolute; left: 3px; top: 12px; width: 16px; height: 16px;
    background: var(--bullet-red); transform: rotate(45deg);
  }
  .page-number { position: absolute; left: 695px; top: 986px; width: 74px; height: 72px; }
</style>
</head>
<body>
<div class="sheet">
  <div class="page-bleed" role="img" aria-label="Photograph of rippling clear blue water with droplets"></div>

  <svg class="crop-marks" width="892" height="1200" aria-hidden="true">
    <g stroke="var(--crop)" stroke-width="1">
      <line x1="0" y1="52" x2="36" y2="52"/><line x1="52" y1="0" x2="52" y2="36"/>
      <line x1="36" y1="74" x2="74" y2="74"/><line x1="74" y1="36" x2="74" y2="74"/>
      <line x1="856" y1="52" x2="892" y2="52"/><line x1="840" y1="0" x2="840" y2="36"/>
      <line x1="818" y1="74" x2="856" y2="74"/><line x1="818" y1="36" x2="818" y2="74"/>
      <line x1="0" y1="1146" x2="36" y2="1146"/><line x1="52" y1="1164" x2="52" y2="1200"/>
      <line x1="36" y1="1126" x2="74" y2="1126"/><line x1="74" y1="1126" x2="74" y2="1164"/>
      <line x1="856" y1="1146" x2="892" y2="1146"/><line x1="840" y1="1164" x2="840" y2="1200"/>
      <line x1="818" y1="1126" x2="856" y2="1126"/><line x1="818" y1="1126" x2="818" y2="1164"/>
    </g>
  </svg>

  <main class="page-content">
    <h1 class="task-title">8. Does It Float?</h1>
    <h2 class="outcome-title">EYLF – Outcome 4: Children are<br>confident and involved learners</h2>

    <p class="lead-in skills">Children develop a range of skills and processes such as problem solving, inquiry, experimenta-<br>tion, hypothesising, researching and investigat-<br>ing when they...</p>
    <p class="body-text children">manipulate objects and experiment<br>with cause and effect, trial and error,<br>and motion</p>

    <p class="lead-in educators">Educators promote this learning when they...</p>
    <p class="body-text educators">plan learning environments with<br>appropriate levels of challenge<br>where children are encouraged<br>to explore, experiment and take<br>appropriate risks in their learning</p>

    <p class="lead-in task">This task provides an opportunity to:</p>
    <ul class="opportunities">
      <li>explore the concepts<br>of “cause” and “effect”</li>
      <li>predict and test hypotheses</li>
      <li>develop awareness<br>of natural phenomena</li>
    </ul>

    <svg class="page-number" viewBox="0 0 74 72" aria-label="Page 16">
      <polygon points="37,0 74,27 60,72 14,72 0,27" fill="var(--ink-navy)"/>
      <text x="37" y="51" text-anchor="middle" font-family="Didact Gothic, sans-serif" font-size="34" fill="#ffffff">16</text>
    </svg>
  </main>
</div>
</body>
</html>
```